Dentistry Office

We want a new design for a Dentist's office website.

The theme is: "We provide high quality, state-of-the-art, dental care in a comfortable, caring environment."

The site currently has a menu on the left of the page with about 40 items on it. There is a great deal of textual content on each page, plus several illustrations.

We want to do this using CSS, so we need specifications in the CSS for all possible elements. The CSS needs to be named in a logical manner for easy use.

Every dentist on the planet seems to use lots of Flash. We don't want to because it is so distracting. We are looking for an elegant solution targeting 24-55 age group, but not excluding anyone.

The following (from another dentist's site) can give you a taste of what we want to communicate on the site:

"After 20 years of teaching dentists how to refine their technique and many years of writing textbooks, I currently devote my time to my office and the hands-on practice of dentistry. I'd like to welcome you personally to my dental practice, and I invite you to meet my highly experienced team of professionals.

"We have offered complete dental care of the highest quality since 1978. We provide Preventive Services, Tooth Whitening and Cosmetic Dentistry for a beautiful smile, Endodontics (root canal treatment) to treat painful teeth, Sedation Dentistry so you can relax, and Dental Implants to restore what is missing. We offer total care.

"Our approach to your health is simple: We use our education, experience and dedication to provide every patient with superior dental care.

"This passion for excellence is not just a goal, but a standard every member of our team holds.

"We also pride ourselves with our state of the art procedures, training and technology. This includes creating a beautiful smile using techniques that preserve as much of the original tooth as possible.

"Our abilities are renowned throughout the dental profession and I hope if you have any questions you will contact us by an e-mail note, by phone or just by dropping by."

Keep in mind the screen shape and dimensions. Your design needs to work in the normal screen proportions, regardless of how it looks when you post it here. Scrolling is OK, but the first impression needs to work.
Updates

Keep in mind that there will be about 250 words, or more, on each page.

Competitors web sites:

http://www.brindlecovedentist.example/

http://www.brindlecovedentalcare.example/

http://www.grinsbymarlowvaledental.example/

http://www.tenbyfamilydentalcare.example/

http://www.quelmardental.example/

http://www.dovrinadental.example/

We need to compete with these.

Target Market(s)

Generally adults seeking the most experienced and comfortable-to-be-with dentist.

Industry/Entity Type

Training

Requirements
Must have
• Must stand apart from other dentists.
• Must be elegant.
• Must have a horizontal menu structure across all columns, NOT a vertical that requires scrolling, no popout, pop down, etc. menus.
• We are looking for something special.
• Do not waste your time or ours putting up templates and things you have used before.
• Personally, I do not see how someone outside the US can understand the northern California dental market. But you are welcome to try.
Should not have
• Flash or graphics that move
• The look of a template
• Folksy fonts
• Looks like you used it 20 times before

```html
<!DOCTYPE html>
<html lang="en">
<head>
<meta charset="utf-8">
<title>What Are Your Dental Challenges? | Dr. Wendell</title>
<link href="https://fonts.googleapis.com/css2?family=Arimo:ital,wght@0,400;0,700;1,400;1,700&display=swap" rel="stylesheet">
<style>
:root{
  --page:#333333;
  --panel:#e4e4e4;
  --panel-light:#ebebeb;
  --ink:#1a1a1a;
  --white:#ffffff;
  --pink:#e0207a;
  --magenta:#9b0b5f;
  --night:#000000;
  --divider:#8a8a8a;
  --btn-education:#5a2e90;
  --btn-preventative:#7c2a8e;
  --btn-cosmetics:#8c2c5c;
  --btn-restorations:#c2255e;
  --btn-visiting:#e8175d;
}
*{box-sizing:border-box;margin:0;padding:0}
html,body{width:801px;height:1200px;overflow:hidden}
body{background:var(--page);font-family:"Arimo",Arial,sans-serif;color:var(--ink);position:relative}
.site-nav{position:absolute;left:0;top:0;width:801px;height:33px;background:linear-gradient(#2b2b2b,#141414);display:flex;padding-left:35px}
.site-nav a{color:var(--white);text-decoration:none;font-size:12px;line-height:33px;padding:0 14px;border-right:1px solid #555}
.site-nav a:first-child{border-left:1px solid #555}
.page-title{position:absolute;top:56px;left:0;width:801px;text-align:center;color:var(--pink);font-weight:400;font-size:35px;letter-spacing:-.3px}
.photo{position:absolute;top:118px;height:171px}
.photo-toothache{left:34px;width:239px;background:linear-gradient(135deg,#f3ece8,#c99a8a)}
.photo-fear{left:273px;width:243px;background:linear-gradient(135deg,#f1eeee,#5a3a30)}
.photo-checkup{left:516px;width:244px;background:linear-gradient(135deg,#d9e6ee,#8ea7bb)}
.feature{position:absolute;top:289px;height:210px;padding:5px 6px;font-size:9.2px;line-height:11.5px;overflow:hidden}
.feature h2{font-size:12.5px;line-height:15px;font-weight:700;margin-bottom:3px}
.feature p{margin-bottom:11px}
.feature-toothache{left:34px;width:239px;background:var(--panel-light)}
.feature-toothache h2{color:var(--magenta)}
.feature-toothache .callout{font-size:11px;line-height:13.5px;font-weight:700}
.feature-fear{left:273px;width:243px;background:var(--magenta);color:var(--white)}
.feature-fear a{color:var(--white);font-weight:700;text-decoration:none}
.feature-checkup{left:516px;width:244px;background:var(--page);color:var(--white)}
.feature-checkup h2{color:var(--pink)}
.feature-checkup .cta{color:var(--pink)}
.topic-menu{position:absolute;left:34px;top:499px;width:726px;height:210px;background:var(--night)}
.topic-group{position:absolute;top:21px;width:140px}
.topic-button{display:block;width:120px;height:27px;border-radius:3px;color:var(--white);font-style:italic;font-size:13px;text-align:center;line-height:27px;margin-bottom:10px}
.topic-group ul{list-style:none;padding-left:1px}
.topic-group li{color:var(--white);font-style:italic;font-weight:700;font-size:9.3px;line-height:14.1px;white-space:nowrap}
.g-education{left:19px}.g-education .topic-button{background:var(--btn-education)}
.g-preventative{left:158px}.g-preventative .topic-button{background:var(--btn-preventative)}
.g-cosmetics{left:301px}.g-cosmetics .topic-button{background:var(--btn-cosmetics)}
.g-restorations{left:445px}.g-restorations .topic-button{background:var(--btn-restorations)}
.g-visiting{left:590px}.g-visiting .topic-button{background:var(--btn-visiting);box-shadow:0 0 0 1px #ff8fb0 inset}
.info-panel{position:absolute;left:34px;top:709px;width:726px;height:455px;background:var(--panel)}
.info-col{position:absolute;top:0;height:346px;padding:7px 6px;font-size:9.2px;line-height:11.5px}
.info-col + .info-col{border-left:1px solid var(--divider)}
.info-col h3{color:var(--magenta);font-size:11px;font-weight:700;line-height:13px;margin:6px 0 4px}
.info-col h3.first{margin-top:0}
.info-col p{margin-bottom:10px}
.info-col .link{color:var(--magenta);font-weight:700}
.col-smile{left:0;width:149px}
.col-mercury{left:149px;width:146px}
.col-fillings{left:295px;width:154px}
.col-consult{left:449px;width:277px}
.media-slot{width:134px;height:90px;background:#1b1b1b;color:var(--white);font-size:7.2px;font-weight:700;line-height:9px;padding:8px 8px}
.footer-links{position:absolute;left:6px;top:357px;font-size:10.5px;font-weight:700;color:var(--magenta)}
.footer-links p{margin-bottom:14px}
.footer-offer{position:absolute;left:202px;top:357px;font-size:10.5px;line-height:13px}
.footer-offer small{display:block;font-size:7.3px;line-height:9px}
.footer-offer p{margin-bottom:14px}
.blossom{position:absolute;left:496px;top:225px;width:230px;height:140px;background:radial-gradient(ellipse at 75% 55%,rgba(90,90,90,.35),rgba(228,228,228,0) 70%)}
</style>
</head>
<body>
<nav class="site-nav">
  <a href="#">Home page</a><a href="#">Why we are different</a><a href="#">Technologies we offer</a><a href="#">Meet Dr. Wendell</a><a href="#">Our Staff</a><a href="#">Contact us/Links</a>
</nav>

<h1 class="page-title">What Are Your Dental Challenges?</h1>

<div class="photo photo-toothache" role="img" aria-label="Photo of a woman holding her cheek in toothache pain"></div>
<div class="photo photo-fear" role="img" aria-label="Photo of a woman covering her face in fear"></div>
<div class="photo photo-checkup" role="img" aria-label="Photo of a dentist reviewing x-rays with a patient"></div>

<section class="feature feature-toothache">
  <h2>Toothache?</h2>
  <p>Toothaches are about as bad a pain as you can experience. We know and we sympathize.<br>That's why we make every effort to bring you immediate relief by keeping room in our schedule for this type of emergency.<br>Give us a call right now at (555) 014-2290 and we'll get you in TODAY!</p>
  <p class="callout">Toothaches can largely be avoided with proper preventive care.</p>
</section>

<section class="feature feature-fear">
  <h2>Deathly Fear of Dentist?</h2>
  <p>With today's technologies that is no longer an excuse. You can be blissfully asleep while even major procedures are performed. When you wake up, everything is done and you're on your way. We specialize in sedation dentistry, also known as sleep dentistry, and you can learn more by clicking here.<br><a href="#">http://www.drwendell.example/<br>sleepdentistrycalder.htm</a></p>
  <p>Give us a call right now at (555) 014-2290 and make an appointment!</p>
</section>

<section class="feature feature-checkup">
  <h2>Dental Check-Ups</h2>
  <p>Dental check-ups and removal of plaque and tartar from your teeth are the cornerstone of good dental health. Not only can you prevent most toothaches, you may be surprised at how much better and more energetic your entire body feels. Low-grade infections may be lurking in your gums and sapping your energy. See more information by visiting our pages under Preventative in the left side bar.</p>
  <p>Dental check-ups should become a routine habit and be done at least every six months. You will also save a lot of money by avoiding the cost of major dental work incurred by neglect of your dental health.</p>
  <p class="cta">Give us a call right now at (555) 014-2290 and make an appointment!</p>
</section>

<nav class="topic-menu">
  <div class="topic-group g-education"><span class="topic-button">Education</span>
    <ul><li>Emergency Dental Care</li><li>Your Mouth</li><li>Your Tooth</li><li>Cracked Tooth?</li><li>Missing a Tooth?</li><li>Sensitive Teeth</li><li>Dry Mouth</li><li>Tooth Grinding</li><li>Sleep Dentistry</li><li>Videos</li></ul></div>
  <div class="topic-group g-preventative"><span class="topic-button">Preventative</span>
    <ul><li>What is Preventive Care?</li><li>Taking Care of Your Teeth</li><li>Eating Right</li><li>Dental Check-Ups</li><li>Sealants</li><li>Periodontal Disease</li><li>Kicking the Habit</li><li>Night Guards</li><li>Dental X-Rays</li><li>Antibiotics with Treatment</li></ul></div>
  <div class="topic-group g-cosmetics"><span class="topic-button">Cosmetics</span>
    <ul><li>Cosmetic Dentistry</li><li>Bleaching and Whitening</li><li>Cosmetic Bonding</li><li>Esthetic Veneers</li><li>Tooth Shaping</li></ul></div>
  <div class="topic-group g-restorations"><span class="topic-button">Restorations</span>
    <ul><li>Crowns/Caps: Each Step</li><li>CMBRs</li><li>Porcelain Bridges</li><li>Bonded Dental Bridges</li><li>Gold Restorations</li><li>Implants</li><li>Treating Cracked Teeth</li><li>Periodontal (gum) Treatment</li></ul></div>
  <div class="topic-group g-visiting"><span class="topic-button">Visiting our office</span>
    <ul><li>Where to Stay</li><li>First Visit / Map</li><li>Financial Policy</li><li>Dental Insurance</li></ul></div>
</nav>

<main class="info-panel">
  <section class="info-col col-smile">
    <div class="media-slot">before/after pictures from Cosmetic Dentistry &amp; Bleaching &amp; Whitening</div>
    <h3>Who do you think will get the date or have the winning job interview?</h3>
    <p>When face-to-face with an important person, nothing speaks louder than a winning smile. Crooked teeth, gaps in your teeth or stains are NOT part of a winning smile. Learn more about our cosmetic dentistry services by clicking on the pages under Cosmetics in the above menu.</p>
  </section>
  <section class="info-col col-mercury">
    <div class="media-slot">pictures of amalgam-filled teeth and a patient getting conventional x-rays</div>
    <h3>Concerned about Mercury Amalgams and Radiation Exposure?</h3>
    <p>You are wise to take your health into your own hands and question the things that have been accepted by patients without question in the past. Amalgams, the so-called silver fillings, are a technology that is over 100 years old. It was cheap, and it lasted a long time. Because of the toxic mercury content of amalgams, we no longer use this technology. We use only the finest, modern tooth-colored bonding materials available.</p>
  </section>
  <section class="info-col col-fillings">
    <h3 class="first">Removal of Silver Fillings</h3>
    <p>Many of our patients take preventive action and have their old amalgam fillings removed and replaced with modern materials. We take great care when removing the old material so that the toxic mercury contained in amalgams does not come into contact with the inside of your mouth.</p>
    <h3>Radiation-Free Diagnostics</h3>
    <p>X-ray- free decay diagnostics does exist, and we offer this latest technology. It's called Optical Transillumination. Ultra high-speed radiographs for near zero X-ray exposure are also available. <span class="link">Click here</span> to learn more about all of the latest technologies available at Dr. Wendell.</p>
    <p>If you are a health-conscious patient, give us a call right now at (555) 014-2290 and make an appointment!</p>
  </section>
  <section class="info-col col-consult">
    <h3 class="first">Free Dental Consultations</h3>
    <p>Let us take a look at your dental challenges, and we will prepare a treatment plan at no cost or obligation to you.</p>
    <p>Give us a call right now at (555) 014-2290 and make an appointment for a free dental consultation!</p>
    <h3>Are you ready to stack the odds in your favor?</h3>
    <p>Give us a call right now at (555) 014-2290 and make an appointment!</p>
    <div class="blossom" role="img" aria-label="Illustration of a dark blossoming branch"></div>
  </section>

  <div class="footer-links"><p>Office Hours and Map to Office</p><p>Where to stay?</p></div>
  <div class="footer-offer">
    <p>We offer an Initial Patient Examination, X-rays and Cleaning for $79.00.<small>**New patients only. Offers are cash patients only. Insurance will be billed at full value.</small></p>
    <p>Please contact us at (555) 014-2290.</p>
    <p>To contact us outside office hours for an emergency, please call (555) 014-7731.</p>
  </div>
</main>
</body>
</html>
```